Zelvo Stationary

Design the stationary of Zelvo Promotions Group.

Zelvo is a BTL company, BTL meaning "below the line". In other words Zelvo is a Promotional Marketing company (the company that design the brands promotional activities).

The design should transmit creativity, agility, boldness.

I need:
* Bis Card
* Letter head
* Envelopes, both vertical and horizontal (for legal size), and letter envelope
* Folders
* PPT template (Title page and regular page)
* CD slip (CD envelope)
* ID card (employee card)

And what ever else you want to throw in.
Updates

Guys,

Something I missed from the brief.   The predominat color should be RED.

Also, have fun and play with the exclamation mark (!) of the logo. 

Hi guys, more comments:

Remember that Zelvo is a "creativity" agency, not in the advertising side but on the promotional side, and that should reflect on the stationary.

 I want a bold design.  Bold and yet crisp.

 

Guys, i just uploaded the Logo in AI format.

I Also uploaded the actual Zelvo Bis Card, wich I like.  So I will like to see some designs with that bis card approach.

Guys, I am so sorry, but I notice in your last post that I upladed a wrong design ("13154_promotions_group_zelvo_brief225630.ai").  The problem was that I asked the designer the file in AI format and he send me thw wrong file, and since I dont have Illustrator I could not verify it.

The differences are minor, I just already ask him the correct one (similar to the EPS file).

Sorry                                   

Just post the correct AI file : "Zelvo Logo.ai"

Reason: I'm expecting more designs to choose from and also I wont be available tomorrow to decide.

Reason: Sorry guys, but we are not there yet!

Target Market(s)

Marketing directors, Marketing Managers

Industry/Entity Type

Legal

Requirements
Must have
• Must work with the logo attached.
The predominat color should be RED.
Play and have fun with the exclamation mark (!).
Should not have
• * No old fonts

Should not be:
* boring
* Informal
* rigid

```html
<!DOCTYPE html>
<html lang="en">
<head>
<meta charset="utf-8">
<title>Zelvo Promotions Group – Stationery</title>
<link href="https://fonts.googleapis.com/css2?family=Open+Sans:wght@400;600;800&display=swap" rel="stylesheet">
<style>
:root{
  --backdrop:#c3b399;
  --red:#d72a2f;
  --red-deep:#c4232a;
  --red-soft:#e56a6e;
  --peach:#f4c9b8;
  --grey:#9a9a9a;
  --grey-light:#d7d7d7;
  --grid:#c8c8c8;
  --ink:#2b2b2b;
  --paper:#ffffff;
}
*{box-sizing:border-box;margin:0;padding:0}
html,body{width:1200px;height:871px;overflow:hidden}
body{background:var(--backdrop);font-family:"Open Sans",Arial,sans-serif;color:var(--ink);position:relative}
.piece{position:absolute}
.wordmark{font-family:"Open Sans",Arial,sans-serif;font-weight:800;letter-spacing:-.5px;line-height:1;display:inline-flex;align-items:center;gap:3px}
.wordmark .dot{display:inline-block;border-radius:50%;background:currentColor}

/* envelopes */
.envelope-back{left:0;top:30px;width:385px;height:348px;background:var(--red);overflow:hidden}
.envelope-back .inner-line{position:absolute;left:8px;top:8px;right:8px;bottom:8px;border:1px solid rgba(255,255,255,.35)}
.envelope-back .accent{position:absolute;left:-30px;bottom:-40px;width:150px;height:150px;border-radius:50%;border:10px solid rgba(255,255,255,.25)}
.envelope-front{left:57px;top:93px;width:339px;height:224px;background:var(--paper);border:1px solid var(--red);overflow:hidden}
.envelope-front .flap{position:absolute;left:0;top:0;width:100%;height:22px;border-bottom:1px solid var(--red)}
.envelope-front .return{position:absolute;left:10px;top:40px;font-size:4.5px;line-height:1.4;color:var(--ink)}
.envelope-front .logo{position:absolute;left:200px;top:26px;color:var(--ink);font-size:13px}
.envelope-front .stamp{position:absolute;left:254px;top:50px;width:25px;height:34px;border:1.5px solid var(--ink)}
.envelope-front .address-line{position:absolute;left:196px;width:56px;height:1px;background:var(--ink)}
.envelope-front .accent{position:absolute;left:-50px;top:110px;width:120px;height:120px;border-radius:50%;border:12px solid var(--red)}

/* slides */
.slide-title{left:621px;top:14px;width:280px;height:207px;background:var(--red);overflow:hidden}
.slide-title .accent{position:absolute;left:40px;top:-30px;width:110px;height:110px;border-radius:50%;border:14px solid rgba(255,255,255,.25)}
.slide-title .stripe{position:absolute;top:40px;width:1px;height:80px;background:rgba(255,255,255,.45)}
.slide-title .title{position:absolute;left:90px;top:164px;color:var(--paper);font-size:17px;font-weight:400}
.slide-content{left:915px;top:14px;width:285px;height:207px;background:var(--paper);overflow:hidden}
.slide-content .band{position:absolute;left:0;top:0;width:57px;height:100%;background:var(--red)}
.slide-content .band .wordmark{position:absolute;left:6px;bottom:12px;color:var(--paper);font-size:12px}
.slide-content .accent{position:absolute;left:80px;top:10px;width:130px;height:130px;border-radius:50%;border:16px solid var(--grey-light)}
.ppt-label{left:830px;top:228px;font-size:11px;letter-spacing:.3px;color:var(--ink)}

/* cd sleeve */
.cd-sleeve{left:7px;top:471px;width:127px;height:391px}
.cd-sleeve .front{position:absolute;left:0;top:0;width:100%;height:171px;background:var(--red-deep);border-bottom:1px solid rgba(255,255,255,.35)}
.cd-sleeve .front .pattern{position:absolute;inset:0;background:linear-gradient(180deg,#d63036,#c8262c)}
.cd-sleeve .front .wordmark{position:absolute;left:22px;top:86px;color:var(--paper);font-size:18px}
.cd-sleeve .back{position:absolute;left:0;top:171px;width:100%;height:220px;background:var(--red)}
.cd-sleeve .back .wordmark{position:absolute;left:40px;bottom:6px;color:var(--paper);font-size:7px}

/* folder */
.folder{left:423px;top:259px;width:376px;height:587px;transform:rotate(-1deg);overflow:hidden;background:var(--red)}
.folder .pocket-top{position:absolute;left:0;top:0;width:100%;height:100px;background:var(--paper)}
.folder .notch{position:absolute;left:170px;top:70px;width:56px;height:56px;border-radius:50%;background:var(--paper)}
.folder .logo{position:absolute;left:155px;top:24px;color:var(--ink);font-size:14px}
.folder .pattern{position:absolute;left:0;top:100px;width:100%;height:487px;background:linear-gradient(180deg,#d9343a,#cd272d)}
.folder .big-name{position:absolute;left:60px;top:290px;color:var(--paper);font-size:58px}
.folder .big-sub{position:absolute;left:70px;top:350px;color:var(--paper);font-size:20px;letter-spacing:6px;font-weight:400}

/* grid sheet */
.grid-sheet{left:655px;top:380px;width:450px;height:470px;background:var(--paper);transform:rotate(8deg);overflow:hidden;
  background-image:linear-gradient(var(--grid) 1px,transparent 1px),linear-gradient(90deg,var(--grid) 1px,transparent 1px);background-size:43px 43px}
.grid-sheet .accent-grey{position:absolute;left:80px;top:-10px;width:160px;height:160px;border-radius:50%;border:22px solid rgba(150,150,150,.55)}
.grid-sheet .accent-peach{position:absolute;left:100px;top:230px;width:170px;height:170px;border-radius:50%;border:24px solid var(--peach)}
.grid-sheet .logo{position:absolute;right:46px;top:40px;color:var(--ink);font-size:14px}
.grid-sheet .footer{position:absolute;left:110px;bottom:12px;font-size:5px;color:var(--grey);line-height:1.5}

/* letterhead */
.letterhead{left:150px;top:320px;width:450px;height:545px;background:var(--paper);transform:rotate(9deg);overflow:hidden}
.letterhead .brand{position:absolute;left:10px;top:4px;color:var(--grey);font-size:84px;letter-spacing:-3px}
.letterhead .brand-sub{position:absolute;left:14px;top:88px;color:var(--grey);font-size:22px;letter-spacing:9px;font-weight:400}
.letterhead .accent{position:absolute;right:-40px;bottom:-20px;width:170px;height:170px;border-radius:50%;border:22px solid var(--red)}
.letterhead .recipient{position:absolute;left:300px;top:130px;font-size:8px;line-height:1.35;color:var(--ink)}
.letterhead .body{position:absolute;left:36px;top:170px;width:320px;font-size:6px;line-height:1.5;color:var(--ink)}
.letterhead .body p{margin-bottom:7px}
.letterhead .closing{position:absolute;left:300px;top:440px;font-size:6px;line-height:1.6}
.letterhead .footer{position:absolute;left:200px;bottom:10px;font-size:5px;color:var(--grey);line-height:1.5}
</style>
</head>
<body>

<!-- envelopes -->
<div class="piece envelope-back">
  <div class="inner-line"></div>
  <div class="accent"></div>
</div>
<div class="piece envelope-front">
  <div class="flap"></div>
  <div class="return">48 Harbor Lane, Suite 5, Westfield<br>Phone +1 555 014 2290</div>
  <div class="logo wordmark">zelvo<span class="dot" style="width:5px;height:5px"></span></div>
  <div class="stamp"></div>
  <div class="address-line" style="top:112px"></div>
  <div class="address-line" style="top:120px"></div>
  <div class="address-line" style="top:128px"></div>
  <div class="address-line" style="top:136px"></div>
  <div class="accent"></div>
</div>

<!-- presentation slides -->
<div class="piece slide-title">
  <div class="accent"></div>
  <div class="stripe" style="left:190px"></div>
  <div class="stripe" style="left:196px"></div>
  <div class="stripe" style="left:202px"></div>
  <div class="title">Put title here</div>
</div>
<div class="piece slide-content">
  <div class="accent"></div>
  <div class="band"><span class="wordmark">zelvo<span class="dot" style="width:4px;height:4px"></span></span></div>
</div>
<div class="piece ppt-label">PPT TEMPLATES</div>

<!-- cd sleeve -->
<div class="piece cd-sleeve">
  <div class="front">
    <div class="pattern" role="img" aria-label="Repeating brand name pattern in red tones"></div>
    <span class="wordmark">zelvo<span class="dot" style="width:5px;height:5px"></span></span>
  </div>
  <div class="back" role="img" aria-label="Repeating brand name pattern in red tones">
    <span class="wordmark">zelvo</span>
  </div>
</div>

<!-- folder -->
<div class="piece folder">
  <div class="pocket-top"></div>
  <div class="notch"></div>
  <span class="logo wordmark">zelvo<span class="dot" style="width:5px;height:5px"></span></span>
  <div class="pattern" role="img" aria-label="Repeating brand name pattern in red tones"></div>
  <span class="big-name wordmark">zelvo</span>
  <span class="big-sub">PROMOTIONS GROUP</span>
</div>

<!-- grid sheet -->
<div class="piece grid-sheet">
  <div class="accent-grey"></div>
  <div class="accent-peach"></div>
  <span class="logo wordmark">zelvo<span class="dot" style="width:5px;height:5px"></span></span>
  <div class="footer">48 Harbor Lane, Suite 5, Westfield, Harbor County<br>Phone +1 555 014 2290 | www.zelvo-promo.example</div>
</div>

<!-- letterhead -->
<div class="piece letterhead">
  <span class="brand wordmark">zelvo</span>
  <span class="brand-sub">PROMOTIONS GROUP</span>
  <div class="accent"></div>
  <div class="recipient">Name Surname<br>Address 27<br>12345 Country</div>
  <div class="body">
    <p>Dear someone,</p>
    <p>Lorem ipsum is simply dummy text of the printing and typesetting industry. Lorem Ipsum has been the industry's standard dummy text ever since the 1500s, when an unknown printer took a galley of type and scrambled it to make a type specimen book. It has survived not only five centuries, but also the leap into electronic typesetting, remaining essentially unchanged.</p>
    <p>It is a long established fact that a reader will be distracted by the readable content of a page when looking at its layout. The point of using Lorem Ipsum is that it has a more-or-less normal distribution of letters, as opposed to using content here, content here, making it look like readable English.</p>
    <p>At vero eos et accusamus et iusto odio dignissimos ducimus qui blanditiis praesentium voluptatum deleniti atque corrupti quos dolores et quas molestias excepturi sint occaecati cupiditate non provident, similique sunt in culpa qui officia deserunt mollitia animi, id est laborum et dolorum fuga.</p>
  </div>
  <div class="closing">Best regards,<br><br>Dario</div>
  <div class="footer">48 Harbor Lane, Suite 5, Westfield, Harbor County<br>Phone +1 555 014 2290 | www.zelvo-promo.example</div>
</div>

</body>
</html>
```